Meadowfield Baptist Church Banner Design

Designing 6 banners (3 + 3 that will hang on opposite sides of our auditorium) that are 10 feet long by 4 feet wide.

Use our branding guide - specifically item 4 (vertical logo) and item 5 (icon logo).

Design elements found in our KINDLE booklet, we would like to see designs that utilize the white, green and blue colour palettes but NOT the grey. Other colours may be incorporated (e.g. coral).

We are looking for 3 banner designs that would match on either side of the auditorium, the first banner incorporating the word "TRUTH", the second incorporating the word "LOVE", and the third incorporating the word "MISSION".

We interested in incorporating graphics such as trees or outdoor themes.

Font styles to use
Other font styles liked:
• Montserrat

Colors
34a7d7
00a990
f47c35

Requirements
Must have
• Banner Type #1 include the word "TRUTH"
Banner Type #2 include the word "LOVE"
Banner Type #3 include the word "MISSION"

Colour scheme must include CMYK 54 / 5 / 16 / 0 (which is available in the branding guide.) We have selected the three colours, included below in the brief.

From the branding guide - utilize #5 (icon) for the banner.

UPDATE: After reviewing the initial submissions, we are asking for designs that ONLY incorporate #5 - the ICON logo for the banners.
Nice to have
• It would be nice to have some creativity with the colour ... though a more minimalistic style is preferred.

Graphic adaptations such as trees in the background would be of interest.
Should not have
• Colour scheme should not be gray scale.

The banners should NOT be too busy.

Scripture verses (written out) are not necessary.

```html
<!DOCTYPE html>
<html lang="en">
<head>
<meta charset="utf-8">
<title>Meadowfield Baptist Church – Auditorium Banners</title>
<link href="https://fonts.googleapis.com/css2?family=Montserrat:wght@800;900&display=swap" rel="stylesheet">
<style>
  :root {
    --sky: #34a7d7;
    --teal: #00a990;
    --coral: #f47c35;
    --deep: #1b86bd;
    --mid: #2a9bd0;
    --light: #6fcbe9;
    --white: #ffffff;
    --page: #ffffff;
  }
  * { margin: 0; padding: 0; box-sizing: border-box; }
  html, body {
    width: 1200px; height: 935px; overflow: hidden;
    background: var(--page);
    font-family: "Montserrat", Arial, sans-serif;
  }
  .canvas { position: relative; width: 1200px; height: 935px; }

  .banner {
    position: absolute; top: 24px;
    width: 356px; height: 890px;
    overflow: hidden;
  }
  .banner--truth   { left: 22px; }
  .banner--love    { left: 435px; }
  .banner--mission { left: 828px; }

  .banner__texture {
    position: absolute; inset: 0;
    background:
      linear-gradient(180deg,
        var(--deep) 0%, var(--mid) 22%, var(--deep) 38%,
        var(--mid) 52%, var(--light) 66%, var(--mid) 74%, var(--deep) 100%);
  }
  .banner--love .banner__texture {
    background:
      linear-gradient(180deg,
        var(--light) 0%, #9bdcf0 20%, var(--mid) 38%,
        var(--deep) 55%, var(--mid) 75%, var(--deep) 100%);
  }

  .banner__block {
    position: absolute; left: 0; width: 100%; height: 248px;
    display: flex; flex-direction: column;
    align-items: center; justify-content: center; gap: 14px;
  }
  .banner__block--bottom { bottom: 0; }
  .banner__block--top { top: 0; }
  .banner__block--sky { background: var(--sky); }
  .banner__block--teal { background: var(--teal); }
  .banner__block--coral { background: var(--coral); }

  .brand__dot {
    width: 30px; height: 30px; border-radius: 50%;
    background: var(--white);
  }
  .brand__name {
    color: var(--white);
    font-weight: 800; font-size: 22px; line-height: 1.2;
    text-align: center; letter-spacing: 0.04em;
    text-transform: uppercase;
  }

  .banner__frame {
    position: absolute; inset: 19px;
    border: 5px solid var(--white);
    pointer-events: none;
  }

  .banner__word {
    position: absolute; left: 178px;
    color: var(--white);
    font-weight: 900; letter-spacing: 0.02em;
    line-height: 1; white-space: nowrap;
    transform: translate(-50%, -50%) rotate(-90deg);
  }
  .banner--truth .banner__word   { top: 344px; font-size: 122px; }
  .banner--love .banner__word    { top: 578px; font-size: 122px; }
  .banner--mission .banner__word { top: 348px; font-size: 104px; }
</style>
</head>
<body>
<main class="canvas">

  <section class="banner banner--truth">
    <div class="banner__texture" role="img" aria-label="Blue brushstroke paint texture with a faint tree silhouette"></div>
    <h2 class="banner__word">TRUTH</h2>
    <div class="banner__block banner__block--bottom banner__block--sky">
      <span class="brand__dot"></span>
      <p class="brand__name">Meadowfield<br>Baptist Church</p>
    </div>
    <div class="banner__frame"></div>
  </section>

  <section class="banner banner--love">
    <div class="banner__texture" role="img" aria-label="Blue brushstroke paint texture with a faint tree silhouette"></div>
    <div class="banner__block banner__block--top banner__block--teal">
      <span class="brand__dot"></span>
      <p class="brand__name">Meadowfield<br>Baptist Church</p>
    </div>
    <h2 class="banner__word">LOVE</h2>
    <div class="banner__frame"></div>
  </section>

  <section class="banner banner--mission">
    <div class="banner__texture" role="img" aria-label="Blue brushstroke paint texture with a faint tree silhouette"></div>
    <h2 class="banner__word">MISSION</h2>
    <div class="banner__block banner__block--bottom banner__block--coral">
      <span class="brand__dot"></span>
      <p class="brand__name">Meadowfield<br>Baptist Church</p>
    </div>
    <div class="banner__frame"></div>
  </section>

</main>
</body>
</html>
```